Law Offices business card

Hi there, I'll need business card for the Law Offices of Colin Matheny. The information must convey his strategic approach and quick resolution to complex business litigation needs. Please emphasize Civil Litigation, Corporate Law, Business Governance and Real Estate Law. Colin has over 25 years of experience in these fields.The card should be modern and edgy and the message should be clear. Please consult his current website for ideas.

```html
<!DOCTYPE html>
<html lang="en">
<head>
<meta charset="utf-8">
<title>Law Offices of Colin Matheny – Business Card</title>
<link rel="stylesheet" href="https://fonts.googleapis.com/css2?family=Cinzel:wght@400;600&family=Open+Sans:wght@400;600;700&display=swap">
<style>
  :root {
    --backdrop: #9c9c9a;
    --card-black: #050505;
    --accent-orange: #e97a24;
    --swoosh-grey: #c9c9c9;
    --ink-white: #ffffff;
    --card-w: 560px;
    --card-h: 320px;
  }
  * { margin: 0; padding: 0; box-sizing: border-box; }
  html, body {
    width: 1200px; height: 900px; overflow: hidden;
    background: var(--backdrop);
  }
  .canvas {
    position: relative; width: 1200px; height: 900px;
    display: flex; flex-direction: column; align-items: center; justify-content: center; gap: 44px;
  }
  .card {
    position: relative; width: var(--card-w); height: var(--card-h);
    background: var(--card-black); overflow: hidden;
    box-shadow: 0 6px 16px rgba(0,0,0,.25);
  }

  /* Front face */
  .card-front .brand {
    position: absolute; top: 62px; left: 0; right: 0;
    display: flex; align-items: center; justify-content: center; gap: 18px;
  }
  .brand-mark {
    flex: none; width: 80px; height: 80px; border-radius: 50%;
    border: 3px solid var(--ink-white);
  }
  .brand-name {
    font-family: 'Cinzel', serif; font-weight: 400;
    color: var(--accent-orange); font-size: 25px; line-height: 1.15;
    letter-spacing: .06em;
  }
  .services {
    position: absolute; top: 196px; left: 20px; right: 20px; text-align: center;
    font-family: 'Open Sans', sans-serif; font-weight: 600;
    color: var(--ink-white); font-size: 15px; line-height: 1.5;
  }

  /* Back face */
  .card-back .panel-art { position: absolute; inset: 0; }
  .emblem {
    position: absolute; left: 40px; top: 66px; width: 180px; height: 180px;
    border-radius: 50%; border: 4px solid var(--ink-white);
    display: flex; align-items: center; justify-content: center; text-align: center;
    font-family: 'Open Sans', sans-serif; font-weight: 700;
    color: var(--ink-white); font-size: 21px; line-height: 1.2;
  }
  .contact {
    position: absolute; right: 28px; top: 66px; text-align: right;
    font-family: 'Open Sans', sans-serif; color: var(--ink-white);
  }
  .contact-name { font-weight: 700; font-size: 21px; line-height: 1.1; }
  .contact-role { font-size: 14px; margin-bottom: 12px; }
  .contact-address { font-size: 15px; line-height: 1.3; margin-bottom: 12px; }
  .contact-list { list-style: none; font-size: 15px; line-height: 1.55; }
  .contact-list li { display: flex; justify-content: flex-end; align-items: center; gap: 8px; }
  .contact-list svg { flex: none; width: 12px; height: 12px; fill: var(--ink-white); }
</style>
</head>
<body>
<main class="canvas">

  <section class="card card-front" aria-label="Card front">
    <div class="brand">
      <div class="brand-mark"></div>
      <div class="brand-name">Law Offices<br>of Colin Matheny</div>
    </div>
    <p class="services">Civil Litigation | Corporate Law<br>Business Governance | Real Estate Law</p>
  </section>

  <section class="card card-back" aria-label="Card back">
    <svg class="panel-art" viewBox="0 0 560 320" preserveAspectRatio="none" aria-hidden="true">
      <path d="M246,0 C342,75 323,219 162,320 L192,320 C347,219 364,75 276,0 Z" fill="var(--swoosh-grey)"/>
      <path d="M276,0 C364,75 347,219 192,320 L560,320 L560,0 Z" fill="var(--accent-orange)"/>
    </svg>
    <div class="emblem">Colin<br>Matheny</div>
    <div class="contact">
      <p class="contact-name">Colin Matheny</p>
      <p class="contact-role">Attorney</p>
      <p class="contact-address">118B Harbor Avenue<br>Palm Cove, Florida 33410</p>
      <ul class="contact-list">
        <li>561-555-0142
          <svg viewBox="0 0 24 24"><path d="M6.6 10.8a15 15 0 0 0 6.6 6.6l2.2-2.2a1 1 0 0 1 1-.25 11 11 0 0 0 3.6.6 1 1 0 0 1 1 1V20a1 1 0 0 1-1 1A17 17 0 0 1 3 4a1 1 0 0 1 1-1h3.5a1 1 0 0 1 1 1 11 11 0 0 0 .6 3.6 1 1 0 0 1-.25 1Z"/></svg></li>
        <li>561-555-0187
          <svg viewBox="0 0 24 24"><path d="M4 3h16v18H4Zm3 3v4h10V6Zm0 7v2h2v-2Zm4 0v2h2v-2Zm4 0v2h2v-2Zm-8 4v2h2v-2Zm4 0v2h2v-2Zm4 0v2h2v-2Z" fill-rule="evenodd"/></svg></li>
        <li>colin@mathenylaw.com
          <svg viewBox="0 0 24 24"><path d="M2 5h20v14H2Zm2 2v.5l8 5 8-5V7Z"/></svg></li>
        <li>www.mathenylaw.com
          <svg viewBox="0 0 24 24"><circle cx="12" cy="12" r="10"/></svg></li>
      </ul>
    </div>
  </section>

</main>
</body>
</html>
```